SaaS Early tech startup business card design

Unique design for experience ecommerce platform company. the business cards will be used by executive members. conformance with color code is required.

```html
<!DOCTYPE html>
<html lang="en">
<head>
<meta charset="UTF-8">
<title>Velto business card</title>
<link rel="stylesheet" href="https://fonts.googleapis.com/css2?family=Bebas+Neue&family=Poppins:wght@400;500;600&display=swap">
<style>
  :root {
    --backdrop: #9a9a9a;
    --paper: #ffffff;
    --navy: #07668f;
    --ink-blue: #0d5f86;
    --teal: #0bb39a;
    --text-grey: #555a5e;
    --band-1: #0a6592;
    --band-2: #0e6f9b;
    --band-3: #1489a7;
    --band-4: #10a593;
    --band-5: #1ab9a0;
    --band-6: #2fdcb9;
  }
  * { margin: 0; padding: 0; box-sizing: border-box; }
  html, body {
    width: 1200px; height: 1200px; overflow: hidden;
    background: var(--backdrop);
    font-family: "Poppins", sans-serif;
  }
  .card {
    position: absolute;
    left: 262px;
    width: 686px;
    height: 392px;
  }
  .card-front { top: 165px; background: var(--paper); }
  .card-back { top: 653px; background: var(--navy); }

  .brand-name {
    position: absolute;
    font-family: "Poppins", sans-serif;
    font-weight: 600;
    color: var(--ink-blue);
    line-height: 1;
    letter-spacing: -2px;
  }
  .card-front .brand-name { right: 42px; top: 42px; font-size: 104px; }
  .card-back .brand-name {
    left: 0; right: 0; top: 122px;
    text-align: center; font-size: 150px; color: var(--teal);
  }

  .holder-name {
    position: absolute; left: 46px; top: 238px;
    font-family: "Bebas Neue", sans-serif;
    font-size: 35px; line-height: 1;
    color: var(--ink-blue);
  }
  .holder-title {
    position: absolute; left: 46px; top: 268px;
    font-size: 16px; font-weight: 500; color: var(--teal);
  }
  .divider {
    position: absolute; left: 46px; width: 597px; top: 301px;
    height: 1px; background: var(--ink-blue);
  }
  .contact {
    position: absolute;
    font-size: 16px; line-height: 19px; color: var(--text-grey);
  }
  .contact-address { left: 46px; top: 318px; }
  .contact-phone { left: 297px; top: 318px; }
  .contact-web { left: 483px; top: 322px; }
  .contact-line { display: flex; align-items: center; gap: 8px; }
  .contact-line svg { width: 14px; height: 14px; fill: var(--teal); flex: none; }

  .colour-band {
    position: absolute; left: 0; right: 0; bottom: 0; height: 14px;
    display: flex;
  }
  .colour-band span { flex: 1; }
  .colour-band span:nth-child(1) { background: var(--band-1); }
  .colour-band span:nth-child(2) { background: var(--band-2); }
  .colour-band span:nth-child(3) { background: var(--band-3); }
  .colour-band span:nth-child(4) { background: var(--band-4); }
  .colour-band span:nth-child(5) { background: var(--band-5); }
  .colour-band span:nth-child(6) { background: var(--band-6); }
</style>
</head>
<body>
  <section class="card card-front">
    <div class="brand-name">velto</div>

    <h1 class="holder-name">Daniel Reyes</h1>
    <p class="holder-title">President</p>
    <div class="divider"></div>

    <address class="contact contact-address" style="font-style:normal">
      4120 Birchwood Court<br>
      Juneau, Alaska 28613
    </address>

    <div class="contact contact-phone">
      <div class="contact-line">
        <svg viewBox="0 0 24 24" aria-hidden="true"><path d="M6.6 10.8a15.1 15.1 0 0 0 6.6 6.6l2.2-2.2c.3-.3.7-.4 1-.2 1.1.4 2.3.6 3.6.6.6 0 1 .4 1 1V20c0 .6-.4 1-1 1A17 17 0 0 1 3 4c0-.6.4-1 1-1h3.5c.6 0 1 .4 1 1 0 1.3.2 2.5.6 3.6.1.3 0 .7-.2 1z"/></svg>
        <span>481-306-2274</span>
      </div>
      <div class="contact-line">
        <svg viewBox="0 0 24 24" aria-hidden="true"><path d="M7 1h10a2 2 0 0 1 2 2v18a2 2 0 0 1-2 2H7a2 2 0 0 1-2-2V3a2 2 0 0 1 2-2zm0 3v14h10V4zm5 15.5a1.2 1.2 0 1 0 0 2.4 1.2 1.2 0 0 0 0-2.4z"/></svg>
        <span>481-730-1596</span>
      </div>
    </div>

    <div class="contact contact-web">
      <div class="contact-line">
        <svg viewBox="0 0 24 24" aria-hidden="true"><path d="M2 5h20v14H2zm2 2v.4l8 5.2 8-5.2V7zm0 2.8V17h16V9.8l-8 5.2z"/></svg>
        <span>name@velto.com</span>
      </div>
      <div class="contact-line">
        <svg viewBox="0 0 24 24" aria-hidden="true"><path d="M12 2a10 10 0 1 0 0 20 10 10 0 0 0 0-20zm-1 17.9A8 8 0 0 1 4.2 10l4.8 4.8v1a2 2 0 0 0 2 2zm6.9-2.5A2 2 0 0 0 16 16h-1v-3a1 1 0 0 0-1-1H8v-2h2a1 1 0 0 0 1-1V7h2a2 2 0 0 0 2-2v-.4a8 8 0 0 1 2.9 12.8z"/></svg>
        <span>www.velto.com</span>
      </div>
    </div>

    <div class="colour-band">
      <span></span><span></span><span></span><span></span><span></span><span></span>
    </div>
  </section>

  <section class="card card-back">
    <div class="brand-name">velto</div>
  </section>
</body>
</html>
```